Business card design Needed for new logo / Construction business, home extensions and new builds

We need a business card design using our new logo files which i will attach to this project :)

We are a small construction business specialising in home extensions, new builds and property development. We are very ambitious and would appreciate professional and elegant designs for our new business card.

Very serious about using the services on MakerQuarry and recently acquired our new logo from here :)

Please get involved, i will feedback when i can as i am very busy but can respond daily, thanks

Target Market(s)

People that want to build onto their houses, new building developments or adding too their existing property

Industry/Entity Type

Construction

Contact Information for Business Card

Renwick Tolliver Construction, Lionel Ashby (Managing Director), Tel 07822254961, email - info@renwick-tolliver, www.renwick-tolliver.co.uk

Colors

Designer to choose colors to be used in the design.

Requirements
Must have
• I like a deep grey on the back please. A lot of you have provided black from and back, try mixing things up a little. The black looks cool 😎 Thanks

```html
<!DOCTYPE html>
<html lang="en">
<head>
<meta charset="utf-8">
<title>Renwick Tolliver Construction – Business Card</title>
<link href="https://fonts.googleapis.com/css2?family=Lato:wght@400;700;900&display=swap" rel="stylesheet">
<style>
  :root {
    --page: #141414;
    --card-front: #1c1c1c;
    --card-back: #2e2f31;
    --gold: #e0a42e;
    --ink: #141414;
    --white: #e9e9ea;
  }
  * { margin: 0; padding: 0; box-sizing: border-box; }
  html, body { width: 1200px; height: 1200px; overflow: hidden; }
  body { background: var(--page); font-family: "Lato", sans-serif; position: relative; }

  .card {
    position: absolute; left: 250px; width: 700px; height: 400px;
    border-radius: 20px; overflow: hidden;
  }
  .card--front { top: 170px; background: var(--card-front); }
  .card--back { top: 630px; background: var(--card-back); }

  .front__wave { position: absolute; inset: 0; }

  .brand { position: absolute; left: 28px; width 320px; width: 320px; top: 62px; text-align: center; }
  .brand__dot { width: 76px; height: 76px; border-radius: 50%; background: var(--gold); margin: 0 auto 34px; }
  .brand__name {
    font-weight: 700; color: var(--gold);
    font-size: 24px; letter-spacing: 2px; line-height: 1.25; text-transform: uppercase;
  }

  .person { position: absolute; right: 47px; top: 40px; text-align: right; }
  .person__name { font-weight: 900; font-size: 31px; color: var(--white); letter-spacing: 0.5px; line-height: 1; text-transform: uppercase; }
  .person__role { font-weight: 400; font-size: 19px; color: var(--gold); margin-top: 6px; }

  .contact { position: absolute; right: 47px; top: 224px; list-style: none; }
  .contact__item {
    display: flex; justify-content: flex-end; align-items: center;
    font-size: 18px; color: var(--ink); height: 25px;
  }
  .contact__item--address { align-items: flex-start; height: auto; line-height: 25px; margin-bottom: 3px; }
  .contact__text { text-align: right; }
  .contact__icon { width: 14px; height: 14px; margin-left: 13px; flex: none; fill: var(--ink); }
  .contact__item--address .contact__icon { margin-top: 5px; }

  .back__brand { position: absolute; left: 0; right: 0; top: 80px; text-align: center; }
  .back__dot { width: 110px; height: 110px; border-radius: 50%; background: var(--gold); margin: 0 auto 30px; }
  .back__name { font-weight: 700; color: var(--gold); font-size: 30px; letter-spacing: 3px; line-height: 1.25; text-transform: uppercase; }
  .back__web {
    position: absolute; left: 0; right: 0; top: 340px; text-align: center;
    font-size: 16px; letter-spacing: 3px; color: var(--gold); text-transform: uppercase;
  }
</style>
</head>
<body>

<section class="card card--front">
  <svg class="front__wave" viewBox="0 0 700 400" aria-hidden="true">
    <defs>
      <linearGradient id="goldFill" x1="0" y1="0" x2="0" y2="1">
        <stop offset="0" stop-color="#c8861a"/>
        <stop offset="0.45" stop-color="#ffd98a"/>
        <stop offset="0.8" stop-color="#d4921f"/>
        <stop offset="1" stop-color="#e8a62a"/>
      </linearGradient>
      <linearGradient id="silverFill" x1="0" y1="0" x2="1" y2="0">
        <stop offset="0" stop-color="#f2f2f2"/>
        <stop offset="0.3" stop-color="#9ea0a4"/>
        <stop offset="0.7" stop-color="#d8d9dc"/>
        <stop offset="1" stop-color="#9b9da1"/>
      </linearGradient>
    </defs>
    <path d="M0,257 C70,310 120,347 170,347 C260,347 330,265 420,195 C480,150 530,120 583,120 C630,120 670,135 700,150 V400 H0Z" fill="url(#silverFill)"/>
    <path d="M0,290 C60,330 110,357 163,357 C260,357 330,280 420,210 C480,165 530,143 583,143 C630,143 670,160 700,177 V400 H0Z" fill="url(#goldFill)" stroke="#1c1c1c" stroke-width="5"/>
  </svg>

  <div class="brand">
    <div class="brand__dot"></div>
    <p class="brand__name">Renwick Tolliver<br>Construction</p>
  </div>

  <div class="person">
    <h1 class="person__name">Lionel Ashby</h1>
    <p class="person__role">Managing Director</p>
  </div>

  <ul class="contact">
    <li class="contact__item contact__item--address">
      <span class="contact__text">14 Harrow Lane, Leeds<br>West Yorkshire, LS1 4AB</span>
      <svg class="contact__icon" viewBox="0 0 24 24"><path d="M12 1a8 8 0 0 0-8 8c0 6 8 14 8 14s8-8 8-14a8 8 0 0 0-8-8zm0 11a3 3 0 1 1 0-6 3 3 0 0 1 0 6z"/></svg>
    </li>
    <li class="contact__item">
      <span class="contact__text">07822254961</span>
      <svg class="contact__icon" viewBox="0 0 24 24"><path d="M6.6 10.8a15 15 0 0 0 6.6 6.6l2.2-2.2a1 1 0 0 1 1-.25 11 11 0 0 0 3.6.6 1 1 0 0 1 1 1V20a1 1 0 0 1-1 1A17 17 0 0 1 3 4a1 1 0 0 1 1-1h3.5a1 1 0 0 1 1 1 11 11 0 0 0 .6 3.6 1 1 0 0 1-.25 1z"/></svg>
    </li>
    <li class="contact__item">
      <span class="contact__text">info@renwick-tolliver.co.uk</span>
      <svg class="contact__icon" viewBox="0 0 24 24"><path d="M2 5h20v14H2zm2 2v.5l8 5 8-5V7l-8 5z"/></svg>
    </li>
    <li class="contact__item">
      <span class="contact__text">www.renwick-tolliver.co.uk</span>
      <svg class="contact__icon" viewBox="0 0 24 24"><path d="M12 1a11 11 0 1 0 0 22 11 11 0 0 0 0-22zm-1 19.9A9 9 0 0 1 4.2 9.2L9 14v1a2 2 0 0 0 2 2zm6.9-2.5A2 2 0 0 0 16 17h-1v-3a1 1 0 0 0-1-1H8v-2h2a1 1 0 0 0 1-1V8h2a2 2 0 0 0 2-2v-.4a9 9 0 0 1 2.9 12.8z"/></svg>
    </li>
  </ul>
</section>

<section class="card card--back">
  <div class="back__brand">
    <div class="back__dot"></div>
    <p class="back__name">Renwick Tolliver<br>Construction</p>
  </div>
  <p class="back__web">www.renwick-tolliver.co.uk</p>
</section>

</body>
</html>
```